I have a website called Okenta Holdings (okentaholdings.com) that I would like to have redesigned. Most of the content is already created, but I need a new design. You can also see my other website at brambleacres.com. I am open to a new logo or modifying the current logo if you have a good idea. Please feel free to use other images for the home page (and maybe some other locations) if you feel they provide a better look and feel to the website. I prefer a modern look.

Important: You do not have to use the images I've provided for the home page. Feel free to find your own stock photos. You don't have to pay for them unless I select your design.

1) Please use wix.com to make your changes so that I can edit it later.
2) I will need all the graphics files to be saved so I can dowload it for later.
3) I will be adding more content to the site later.
4) This site will likely be transferred over to brambleacres.com so if you make a logo please make one for Okenta Holdings and one for Bramble Acres.
5) You can use other images that you feel would help the look and feel of the website.

```html
<!DOCTYPE html>
<html lang="en">
<head>
<meta charset="utf-8">
<title>Okenta Holdings — Commercial Real Estate Investment and Development</title>
<link href="https://fonts.googleapis.com/css2?family=Montserrat:wght@500;600;700&family=Lato:wght@400;700&display=swap" rel="stylesheet">
<style>
  :root {
    --ink: #111111;
    --text: #2b2b2b;
    --accent: #4a90d9;
    --button: #5b9bd5;
    --navy: #0c2a4f;
    --band: #f5f5f5;
    --badge: #8e8e8e;
    --white: #ffffff;
  }
  * { margin: 0; padding: 0; box-sizing: border-box; }
  html, body { width: 1200px; height: 3673px; overflow: hidden; }
  body { position: relative; background: var(--white); font-family: "Lato", sans-serif; color: var(--text); }
  .abs { position: absolute; }

  /* Header */
  .site-header { left: 0; top: 0; width: 1200px; height: 96px; background: var(--white); }
  .brand { left: 113px; top: 26px; display: flex; align-items: center; gap: 14px; }
  .brand-mark { width: 40px; height: 40px; background: #3d6fb0; }
  .brand-name { font-family: "Lato", sans-serif; font-size: 22px; color: #3d5f8f; letter-spacing: -0.5px; }
  .nav { left: 611px; top: 38px; display: flex; gap: 44px; font-family: "Montserrat", sans-serif; font-size: 15px; font-weight: 500; color: #222; }

  /* Hero */
  .hero { left: 0; top: 96px; width: 1200px; height: 685px;
    background: linear-gradient(180deg, #7fa9cf 0%, #b7b0a2 35%, #8d9aa0 55%, #6fa4bd 70%, #9d9a95 100%); }
  .hero-title { left: 110px; top: 252px; font-family: "Montserrat", sans-serif; font-weight: 700; font-size: 45px; line-height: 64px; color: var(--white); text-transform: uppercase; }
  .hero-sub { left: 110px; top: 463px; font-size: 20px; color: var(--white); }
  .hero-btn { left: 110px; top: 521px; width: 176px; height: 58px; background: var(--button); color: var(--white); font-family: "Montserrat", sans-serif; font-weight: 700; font-size: 15px; display: flex; align-items: center; justify-content: center; border-radius: 3px; }

  /* Feature blocks */
  .photo { width: 338px; height: 455px; }
  .photo-team { left: 203px; top: 847px; background: linear-gradient(180deg, #6c8aa6 0%, #556a80 45%, #8c8a86 100%); }
  .photo-city { left: 647px; top: 1342px; background: linear-gradient(180deg, #8f86c8 0%, #d79ab8 35%, #f2a94e 55%, #8f7e7a 80%, #4d6a3c 100%); }
  .photo-project { left: 203px; top: 1833px; background: linear-gradient(180deg, #3e5f98 0%, #4b5868 45%, #7a7c80 75%, #5b5e62 100%); }
  .section-title { font-family: "Montserrat", sans-serif; font-weight: 700; font-size: 34px; color: var(--ink); }
  .section-body { font-size: 15px; line-height: 25.7px; color: var(--text); width: 406px; hyphens: auto; -webkit-hyphens: auto; }
  .learn-link { font-family: "Montserrat", sans-serif; font-weight: 700; font-size: 15px; color: var(--accent); text-decoration: underline; }

  /* Partners */
  .partners { left: 0; top: 2375px; width: 1195px; height: 337px; background: var(--band); }
  .partners-title { left: 0; top: 2430px; width: 1200px; text-align: center; }
  .partner-badge { top: 2556px; height: 30px; background: var(--badge); border-radius: 3px; }

  /* Map */
  .map { left: 0; top: 2712px; width: 1200px; height: 481px;
    background: linear-gradient(120deg, #cfe3cf 0%, #e3e4e6 22%, #e8e8ea 50%, #e1e3e6 78%, #d6e6d4 100%); }

  /* Footer */
  .site-footer { left: 0; top: 3193px; width: 1200px; height: 480px; background: var(--navy); color: var(--white); }
  .foot-title { font-family: "Montserrat", sans-serif; font-weight: 700; font-size: 25px; color: var(--white); }
  .foot-text { font-size: 15px; line-height: 25.7px; color: var(--white); }
  .field { width: 209px; height: 43px; border: 1px solid #d8dde6; color: var(--white); font-size: 15px; padding: 10px 13px; }
  .field-message { left: 898px; top: 3332px; height: 157px; }
  .submit { left: 1048px; top: 3506px; font-family: "Montserrat", sans-serif; font-weight: 700; font-size: 14px; color: var(--white); }
  .copyright { left: 88px; top: 3600px; }
</style>
</head>
<body>

<header class="abs site-header">
  <div class="abs brand">
    <span class="brand-mark"></span>
    <span class="brand-name">Okenta Holdings</span>
  </div>
  <nav class="abs nav">
    <span>Home</span><span>About</span><span>Strategy</span><span>Projects</span><span>Contact</span>
  </nav>
</header>

<section class="abs hero" role="img" aria-label="Apartment courtyard with a pool and orange lounge chairs"></section>
<h1 class="abs hero-title">Commercial Real Estate<br>Investment and<br>Development Firm</h1>
<p class="abs hero-sub">Building together. Growing Together.</p>
<div class="abs hero-btn">LEARN MORE</div>

<div class="abs photo photo-team" role="img" aria-label="Three partners of the firm standing outdoors"></div>
<h2 class="abs section-title" style="left:584px;top:890px;">About Us</h2>
<p class="abs section-body" lang="en" style="left:584px;top:947px;">Bramble Acres is a private real estate firm that specializes in the procurement, development, management, and disposition of various commercial real estate asset types including multifamily, industrial, single-family, hospitality, self-storage, and flex. The firm effectuates its strategy by utilizing long-standing relationships to ascertain acquisition and development opportunities within a specific target market.&nbsp; Bramble Acres is currently focused on acquisition and development opportunities in the southern portion of the United States.</p>
<span class="abs learn-link" style="left:584px;top:1231px;">LEARN MORE</span>

<h2 class="abs section-title" style="left:196px;top:1405px;">Strategy</h2>
<p class="abs section-body" lang="en" style="left:196px;top:1463px;width:410px;">Bramble Acres evaluates opportunities with a two-pronged approach. First, the firm searches for development opportunities which are in growing metropolitan markets and possess a high barrier to entry. Second, the firm actively purses the acquisition of distressed or value-add assets which yield compelling cash-on-cash returns. The diverse background of the firm avails an opportunistic and entrepreneurial evaluation of each transaction.</p>
<span class="abs learn-link" style="left:199px;top:1690px;">LEARN MORE</span>
<div class="abs photo photo-city" role="img" aria-label="City skyline at sunset"></div>

<div class="abs photo photo-project" role="img" aria-label="Modern glass building with a reflecting pool at dusk"></div>
<h2 class="abs section-title" style="left:584px;top:1946px;">Projects</h2>
<p class="abs section-body" lang="en" style="left:584px;top:2003px;width:400px;">This is your Project Page. It's a great opportunity to help visitors understand the context and background of your latest work. Double click on the text box to start editing your content and make sure to add all the relevant details you want to share.</p>
<span class="abs learn-link" style="left:584px;top:2150px;">LEARN MORE</span>

<section class="abs partners"></section>
<h2 class="abs section-title partners-title">Corporate Partners</h2>
<span class="abs partner-badge" style="left:189px;width:103px;"></span>
<span class="abs partner-badge" style="left:361px;width:103px;"></span>
<span class="abs partner-badge" style="left:538px;width:104px;"></span>
<span class="abs partner-badge" style="left:701px;width:116px;"></span>
<span class="abs partner-badge" style="left:878px;width:107px;"></span>

<div class="abs map" role="img" aria-label="Street map of downtown Dallas around the headquarters"></div>

<footer class="abs site-footer"></footer>
<h3 class="abs foot-title" style="left:88px;top:3272px;">Inquiries</h3>
<p class="abs foot-text" style="left:88px;top:3318px;">For any inquiries, questions or commendations, please call:<br>(214) 555-0187 or fill out the following form</p>
<h3 class="abs foot-title" style="left:88px;top:3397px;">Headquarters</h3>
<p class="abs foot-text" style="left:88px;top:3448px;">4410 Larkspur Ave. 7th Floor<br>Dallas, Texas 75201</p>
<p class="abs foot-text" style="left:90px;top:3504px;">info@brambleacres.com<br>Tel: (214) 555-0187</p>
<h3 class="abs foot-title" style="left:325px;top:3397px;">Employment</h3>
<p class="abs foot-text" style="left:325px;top:3448px;">To apply for a job with Bramble Acres,<br>please send a cover letter togethe<br>with your C.V. to: info@brambleacres.com</p>

<h3 class="abs foot-title" style="left:675px;top:3270px;">Contact Us</h3>
<div class="abs field" style="left:675px;top:3332px;">Name</div>
<div class="abs field" style="left:675px;top:3389px;">Email</div>
<div class="abs field" style="left:675px;top:3446px;">Subject</div>
<div class="abs field field-message">Messages</div>
<span class="abs submit">SUBMIT</span>

<p class="abs foot-text copyright">©Copyrights 2022 Okenta Holdings &nbsp;|&nbsp;&nbsp;&nbsp; All Rights Reserved</p>

</body>
</html>
```